Halvery Construction Group Website

Need a dynamic corporate website that can be built on with time. We want to get our information out to the world and have a place where customers can submit requests for proposals.

Target Market(s)

Custom home owners and buyers. Architects and Real Estate Agents.

Industry/Entity Type

Construction

Number of Pages Required

3 page

Font styles to use
Serif
Sans Serif

Requirements
Must have
• Company logo, about, company contact information, biography, contact, projects,
• Sleek, modern, clean, attractive design.
• Online form customers can use for filling out a request for project proposal.
• Linkedin hyperlink.
• Uses www.halveryconstructiongroup.example

```html
<!DOCTYPE html>
<html lang="en">
<head>
<meta charset="utf-8">
<title>Halvery Construction Group</title>
<link href="https://fonts.googleapis.com/css2?family=Roboto:wght@300;400;500;700&family=Roboto+Condensed:wght@700&display=swap" rel="stylesheet">
<style>
:root{
  --brand-blue:#0d4fa3;
  --link-blue:#0a3a7e;
  --panel-blue:#1e5faa;
  --orange:#f7931e;
  --orange-light:#fba526;
  --footer:#1b1b1b;
  --white:#ffffff;
}
*{margin:0;padding:0;box-sizing:border-box}
html,body{width:1200px;height:892px;overflow:hidden;font-family:'Roboto',sans-serif;background:var(--white)}
.page{position:relative;width:1200px;height:892px}
.site-header{position:absolute;top:0;left:0;width:1200px;height:85px;border-top:3px solid var(--brand-blue);background:var(--white)}
.brand{position:absolute;left:98px;top:22px;display:flex;align-items:center;gap:10px}
.brand-mark{width:34px;height:34px;background:var(--brand-blue)}
.brand-name{font-family:'Roboto',sans-serif;font-weight:500;font-size:17px;line-height:19px;color:var(--brand-blue);text-transform:uppercase;letter-spacing:1px;width:210px}
.menu-toggle{position:absolute;right:100px;top:33px;display:flex;align-items:center;gap:8px;color:var(--brand-blue);font-weight:700;font-size:16px;text-decoration:none}
.hero{position:absolute;top:85px;left:0;width:1200px;height:504px;background:linear-gradient(160deg,#3e5f8c 0%,#26497c 35%,#1a3d73 60%,#13305c 100%)}
.hero-content{position:absolute;left:94px;top:143px;color:var(--white)}
.hero-title{font-family:'Roboto Condensed',sans-serif;font-weight:700;font-size:37px;letter-spacing:.1px;text-shadow:0 2px 4px rgba(0,0,0,.35)}
.hero-lead{margin-top:16px;font-size:22px;line-height:34px;font-weight:400}
.hero-lead a{color:var(--white);font-style:italic}
.hero-lead .sep{margin:0 10px}
.btn-contact{display:inline-block;margin-top:38px;width:136px;height:44px;line-height:40px;text-align:center;border:2px solid var(--white);border-radius:22px;background:linear-gradient(#fba526,#f58a0b);color:var(--white);font-weight:500;font-size:16px;text-decoration:none}
.slider-dots{position:absolute;right:33px;top:211px;display:flex;flex-direction:column;gap:8px}
.slider-dots span{width:11px;height:11px;border:2px solid var(--white);border-radius:50%}
.slider-dots .active{background:var(--orange);border-color:var(--white)}
.links-panel{position:absolute;top:589px;left:0;width:600px;height:245px;background:linear-gradient(180deg,#225fa7,#1b5cab)}
.link-group{position:absolute;top:37px}
.link-group h3{font-size:17px;font-weight:500;color:var(--white);margin-bottom:17px;text-transform:uppercase}
.link-group ul{list-style:none}
.link-group li{font-size:12.5px;color:var(--white);height:28.5px;display:flex;align-items:flex-start;font-weight:400}
.link-group li::before{content:"›";width:27px;font-size:14px;line-height:13px}
.about-panel{position:absolute;top:589px;left:600px;width:600px;height:245px;background:linear-gradient(135deg,var(--orange-light),var(--orange))}
.about-panel h2{position:absolute;left:70px;top:37px;font-size:17px;font-weight:500;color:var(--white)}
.about-panel .copy{position:absolute;left:70px;top:86px;width:433px;font-size:12px;line-height:22.3px;color:var(--white);font-weight:400;letter-spacing:-.15px;text-align:justify;text-shadow:0 0 1px rgba(120,60,0,.35)}
.about-panel .copy p+p{margin-top:13px}
.about-panel .copy p:last-child{text-align:left}
.read-more{float:right;font-size:12px;color:var(--link-blue);text-decoration:none;text-shadow:none}
.site-footer{position:absolute;top:834px;left:0;width:1200px;height:58px;background:var(--footer);color:var(--white);font-size:12.5px;font-weight:400}
.site-footer .legal{position:absolute;left:98px;top:21px}
.footer-nav{position:absolute;right:100px;top:21px;display:flex}
.footer-nav a{color:var(--white);text-decoration:none}
.footer-nav .sep{margin:0 17px}
</style>
</head>
<body>
<div class="page">
  <header class="site-header">
    <div class="brand">
      <span class="brand-mark"></span>
      <span class="brand-name">Halvery Construction Group</span>
    </div>
    <a class="menu-toggle" href="#">
      <svg width="19" height="17" viewBox="0 0 19 17"><rect y="0" width="19" height="3" fill="#0d4fa3"/><rect y="7" width="19" height="3" fill="#0d4fa3"/><rect y="14" width="19" height="3" fill="#0d4fa3"/></svg>
      MENU
    </a>
  </header>

  <section class="hero" role="img" aria-label="Upward view of glass skyscrapers against a blue sky with an airplane overhead">
    <div class="hero-content">
      <h1 class="hero-title">HALVERY CONSTRUCTION GROUP</h1>
      <p class="hero-lead">2000 Latin words, combined with a handful<br>1200 8542 7730<span class="sep">/</span><a href="#">hello@halvery.example</a></p>
      <a class="btn-contact" href="#">CONTACT US</a>
    </div>
    <div class="slider-dots"><span></span><span></span><span class="active"></span><span></span><span></span></div>
  </section>

  <nav class="links-panel" role="img" aria-label="Faint hard hat on a blue tinted background">
    <div class="link-group" style="left:98px">
      <h3>Projects</h3>
      <ul><li>Commercial</li><li>Residential</li><li>Community</li><li>Location Map</li></ul>
    </div>
    <div class="link-group" style="left:264px">
      <h3>Profile</h3>
      <ul><li>Team</li><li>Process</li><li>Testimonials</li><li>History</li></ul>
    </div>
    <div class="link-group" style="left:422px">
      <h3>Connect</h3>
      <ul><li>Email</li><li>Social Feed</li><li>Network</li><li>Video Channel</li></ul>
    </div>
  </nav>

  <section class="about-panel" role="img" aria-label="Faint building facade on an orange tinted background">
    <h2>WE ARE A CONSTRUCTION GROUP</h2>
    <div class="copy">
      <p>Contrary to popular belief, Lorem Ipsum is not simply random text. It has roots in a piece of classical Latin literature from 45 BC, making it over 2000 years old. Ronald Merriweather, a Latin professor at Hollins-Ashford College</p>
      <p>Contrary to popular belief, Lorem Ipsum is not simply random text. It has roots in a piece of classical Latin literature from 45 BC, making <a class="read-more" href="#">Read More</a></p>
    </div>
  </section>

  <footer class="site-footer">
    <p class="legal">© 2016 Halvery Construction , all rights reserved</p>
    <div class="footer-nav">
      <a href="#">Home</a><span class="sep">|</span>
      <a href="#">About</a><span class="sep">|</span>
      <a href="#">Bio</a><span class="sep">|</span>
      <a href="#">Projects</a><span class="sep">|</span>
      <a href="#">Contact us</a>
    </div>
  </footer>
</div>
</body>
</html>
```